Banner poster with different motifs

I'm looking for 5 banners and posters in A1 format in the same design, or the similarity must be recognizable...
Kept quite simple with different titles.

1 ballet
2 Contemporary Dance
3 high heels
4 Salsa & Bachata & Zouk
5 Hip Hop

Modern bright colors
it is for the entrance so that the students see here is a dance school

The text may also be included in the image
The photos are for guidance only; some are our own, some are purchased. However, we are permitted to use them, including our logo, of course.

```html
<!DOCTYPE html>
<html lang="en">
<head>
<meta charset="utf-8">
<title>High Heels – Dance Class Poster</title>
<link rel="stylesheet" href="https://fonts.googleapis.com/css2?family=Montserrat:wght@400&family=Oswald:wght@500&family=Poppins:wght@500;800&display=swap">
<style>
  :root {
    --ink-dark: #0b0d12;
    --smoke-magenta: #a3169e;
    --smoke-violet: #4a1f6b;
    --smoke-teal: #1f6f8f;
    --smoke-deep-teal: #0f3a4d;
    --skin-warm: #6b4a3c;
    --white: #ffffff;
    --neon-fill: #b3e9ff;
    --neon-pink: #ff3fd8;
    --neon-blue: #2b3cff;
    --neon-glow: rgba(110, 210, 255, 0.75);
  }
  html, body {
    margin: 0;
    width: 860px;
    height: 1200px;
    overflow: hidden;
    background: var(--ink-dark);
  }
  .poster {
    position: relative;
    width: 860px;
    height: 1200px;
    overflow: hidden;
    background: var(--ink-dark);
  }
  .photo-backdrop {
    position: absolute;
    inset: 0;
    background:
      radial-gradient(ellipse 300px 240px at 40px 60px, var(--smoke-magenta), transparent 70%),
      radial-gradient(ellipse 260px 300px at 0 300px, var(--smoke-violet), transparent 75%),
      radial-gradient(ellipse 380px 420px at 720px 470px, var(--smoke-teal), transparent 72%),
      radial-gradient(ellipse 420px 260px at 200px 760px, var(--smoke-deep-teal), transparent 70%),
      radial-gradient(ellipse 200px 200px at 0 1130px, var(--smoke-violet), transparent 75%),
      radial-gradient(ellipse 120px 520px at 440px 460px, var(--skin-warm), transparent 75%),
      linear-gradient(160deg, #1b0f24 0%, #101820 50%, #0a0d12 100%);
  }
  .title-high {
    position: absolute;
    margin: 0;
    font-family: "Poppins", sans-serif;
    font-weight: 800;
    color: var(--white);
    line-height: 1;
  }
  .title-high span {
    position: absolute;
    font-size: 230px;
    line-height: 1;
  }
  .letter-h1 { left: 298px; top: 60px; }
  .letter-i  { left: 482px; top: 253px; }
  .letter-g  { left: 238px; top: 413px; }
  .letter-h2 { left: 455px; top: 577px; opacity: 0.92; }
  .title-heels {
    position: absolute;
    left: 70px;
    top: 790px;
    width: 750px;
    height: 290px;
    overflow: visible;
  }
  .heels-outline {
    font-family: "Oswald", sans-serif;
    font-weight: 500;
    fill: none;
    stroke: url(#neonStroke);
    stroke-width: 5;
  }
  .heels-fill {
    font-family: "Oswald", sans-serif;
    font-weight: 500;
    fill: var(--neon-fill);
    stroke: url(#neonStroke);
    stroke-width: 2.5;
    filter: drop-shadow(0 0 10px var(--neon-glow)) drop-shadow(0 0 22px var(--neon-glow));
  }
  .brand {
    position: absolute;
    left: 610px;
    top: 70px;
    width: 180px;
    text-align: center;
    color: var(--white);
    font-family: "Montserrat", sans-serif;
    font-weight: 400;
  }
  .brand-circle {
    display: block;
    width: 58px;
    height: 58px;
    margin: 0 auto 10px;
    border: 1.5px solid var(--white);
    border-radius: 50%;
    box-sizing: border-box;
  }
  .brand-name {
    margin: 0;
    font-size: 25px;
    letter-spacing: 1.5px;
    line-height: 1;
  }
  .brand-tagline {
    margin: 5px 0 0;
    font-size: 7.5px;
    letter-spacing: 2.4px;
    line-height: 1;
  }
  .website {
    position: absolute;
    left: 0;
    right: 0;
    top: 1124px;
    margin: 0;
    text-align: center;
    color: var(--white);
    font-family: "Poppins", sans-serif;
    font-weight: 500;
    font-size: 27px;
    line-height: 1;
    letter-spacing: 3.5px;
  }
</style>
</head>
<body>
  <main class="poster">
    <div class="photo-backdrop" role="img" aria-label="Photo: a dancer in black sportswear and thigh-high platform heel boots posing with raised arms amid magenta and teal stage smoke"></div>

    <h1 class="title-high" aria-label="High">
      <span class="letter-h1">H</span>
      <span class="letter-i">I</span>
      <span class="letter-g">G</span>
      <span class="letter-h2">H</span>
    </h1>

    <svg class="title-heels" viewBox="0 0 750 290" aria-label="Heels">
      <defs>
        <linearGradient id="neonStroke" x1="0" y1="0" x2="1" y2="1">
          <stop offset="0" stop-color="var(--neon-pink)"/>
          <stop offset="0.55" stop-color="#8a3cff"/>
          <stop offset="1" stop-color="var(--neon-blue)"/>
        </linearGradient>
      </defs>
      <text class="heels-outline" x="19" y="279" font-size="320" textLength="716" lengthAdjust="spacingAndGlyphs">HEELS</text>
      <text class="heels-fill" x="15" y="275" font-size="320" textLength="716" lengthAdjust="spacingAndGlyphs">HEELS</text>
    </svg>

    <div class="brand">
      <span class="brand-circle" aria-hidden="true"></span>
      <p class="brand-name">MOVIDORA</p>
      <p class="brand-tagline">DANCE STUDIO RIVERTON</p>
    </div>

    <p class="website">www.movidora-dance.com</p>
  </main>
</body>
</html>
```